ourTradeLoop Webdesign - trading your electronics for cash - helping you clear up clutter

We need web design (and an updated logo) for a new company based in London called "ourTradeLoop". It is a platform that enables users to sell their old electronics for cash, either for themselves or they can donate the cash to charity. In time, we also plan to enable buying of electronics on the site. We specialise in mobile phones, tablets, laptops, and games consoles. Please review brindlo.com, which is a US site with the same business, and also tunefernwick.co.uk, so have a similar business in the UK. We would like to see designs that use the colour red, and that are bold. We currently have a logo, and a WIP site built, but the design needs to be dramatically improved, the right colour mix needs to be chosen to give a clean and modern feel. Please review www.ourtradeloop.com to get an understanding of the work that needs to be improved.

Target Market(s)

People who buy electronics frequently, i.e. upgrade every time a new quince product comes out! These guys usually have a lap top, desk top, tablet and phone.

Industry/Entity Type

Electronics

Logo Text

ourTradeLoop

Number of Pages Required

3 page

Font styles to use
Sans Serif

Colors
ec1f27

Requirements
Must have
• Home page design
• "How-it-works" page design
• Sell page design
• Must use the colour red, and have a secondary/accent colour.

```html
<!DOCTYPE html>
<html lang="en">
<head>
<meta charset="utf-8">
<title>ourTradeLoop – Sell your electronics for cash</title>
<link href="https://fonts.googleapis.com/css2?family=Roboto:wght@300;400;500;700&display=swap" rel="stylesheet">
<style>
:root{
  --red:#ea2a33;
  --red-dark:#cf1f28;
  --red-soft:#ef4f56;
  --navy:#363a5a;
  --blue:#2f8fd8;
  --ink:#333640;
  --muted:#8a8d96;
  --line:#e2e3e6;
  --light:#f3f3f4;
  --white:#ffffff;
}
*{box-sizing:border-box;margin:0;padding:0}
html,body{width:1200px;height:2520px;overflow:hidden;background:var(--white)}
body{font-family:'Roboto',sans-serif;color:var(--ink)}
.page{position:relative;width:1200px;height:2520px;overflow:hidden}
a{color:inherit;text-decoration:none}
ul{list-style:none}

/* top navigation */
.topnav{position:absolute;top:0;left:0;width:1200px;height:110px;display:flex;align-items:center;justify-content:flex-end;padding-right:110px;gap:34px;font-size:14px;font-weight:500;color:var(--ink)}
.topnav .how{display:flex;align-items:center;gap:8px}
.topnav .how i{width:18px;height:18px;border-radius:50%;background:var(--red);display:inline-block}
.btn{display:inline-flex;align-items:center;justify-content:center;border-radius:24px;color:var(--white);font-weight:500;letter-spacing:1px}
.btn-navy{background:var(--navy)}
.btn-red{background:var(--red)}
.topnav .btn{width:100px;height:40px;font-size:14px}
.topnav .link{letter-spacing:1px}
.topnav .register{margin-left:40px}

/* hero */
.hero{position:absolute;top:110px;left:0;width:1200px;height:530px}
.hero-panel{position:absolute;left:0;top:0;width:620px;height:530px;background:var(--red);color:var(--white);text-align:center}
.hero-devices{position:absolute;left:180px;top:40px;width:260px;height:170px;border-radius:8px;background:linear-gradient(135deg,var(--red-soft),var(--red-dark))}
.brand{position:absolute;left:0;width:620px;top:228px;font-size:34px;font-weight:500;display:flex;justify-content:center;align-items:center;gap:12px}
.brand .mark{width:22px;height:22px;background:var(--white)}
.hero-copy{position:absolute;left:90px;width:440px;top:292px;font-size:16px;line-height:1.5;font-weight:300}
.hero-actions{position:absolute;left:0;width:620px;top:390px;display:flex;justify-content:center;align-items:center;gap:22px;font-size:14px}
.hero-actions .btn{width:140px;height:48px;font-size:16px}
.hero-photo{position:absolute;left:620px;top:0;width:580px;height:530px;background:linear-gradient(135deg,#c9b9a4 0%,#8e7d6a 45%,#5b5049 100%)}

/* products */
.tabs{position:absolute;top:690px;left:0;width:1200px;display:flex;justify-content:center;align-items:center;gap:20px;font-size:22px;font-weight:500}
.tab-buy{position:relative;background:var(--red);color:var(--white);padding:10px 26px;border-radius:6px}
.tab-buy:after{content:"";position:absolute;left:50%;bottom:-10px;margin-left:-10px;border-left:10px solid transparent;border-right:10px solid transparent;border-top:10px solid var(--red)}
.tab-sell{color:var(--blue)}
.tab-rule{position:absolute;top:752px;left:60px;width:1080px;height:1px;background:var(--line)}
.product{position:absolute;top:790px;text-align:center;font-size:13px;font-weight:500;letter-spacing:.5px}
.product .shot{margin:0 auto 20px;border-radius:14px;height:200px}
.phone-a{left:80px;width:140px}
.phone-a .shot{width:100px;background:linear-gradient(160deg,#6fa8d8,#1f2f4a)}
.phone-b{left:300px;width:140px}
.phone-b .shot{width:100px;background:linear-gradient(160deg,#e9eaee,#9aa3b5)}
.pad{left:470px;width:180px}
.pad .shot{width:150px;background:linear-gradient(160deg,#5a6f92,#1d2233)}
.book{left:700px;width:400px}
.book .shot{width:360px;border-radius:6px;background:linear-gradient(160deg,#b27cd0,#3c2a6a)}

/* why us */
.why{position:absolute;top:1130px;left:0;width:1200px;height:400px;background:var(--light)}
.why h2{position:absolute;top:60px;width:1200px;text-align:center;color:var(--red);font-size:26px;font-weight:500;letter-spacing:1px}
.why .rule{position:absolute;top:108px;left:420px;width:360px;height:1px;background:#d5d6d9}
.feature{position:absolute;top:150px;width:300px;text-align:center}
.feature-delivery{left:120px}
.feature-payment{left:450px}
.feature-refund{left:780px}
.feature svg{display:block;margin:0 auto 24px}
.feature h3{font-size:16px;font-weight:700;letter-spacing:.5px;margin-bottom:14px}
.feature p{font-size:13px;line-height:1.6;color:var(--muted)}

/* tweets */
.tweets{position:absolute;top:1590px;left:60px;width:680px;height:260px}
.tweets h2{font-size:26px;font-weight:500;color:var(--red)}
.tweets .rule{margin-top:14px;height:1px;background:var(--line)}
.arrows{position:absolute;right:0;top:6px;display:flex;gap:6px}
.arrows span{width:28px;height:28px;border:1px solid var(--line);display:flex;align-items:center;justify-content:center;font-size:14px;color:var(--muted)}
.tweet{position:absolute;top:80px;width:320px;font-size:13px}
.tweet-first{left:0}
.tweet-second{left:350px}
.tweet .who{display:flex;align-items:center;gap:10px;margin-bottom:14px}
.tweet .avatar{width:30px;height:30px;border-radius:50%;background:var(--blue)}
.tweet .name{font-weight:700;font-size:13px}
.tweet .handle{color:var(--muted);font-size:12px}
.tweet .time{margin-left:auto;color:var(--muted);font-size:12px}
.tweet p{line-height:1.6;color:var(--muted)}
.social-box{position:absolute;top:1600px;left:800px;width:340px;height:250px;border:1px solid var(--line);padding:20px}
.social-box .head{display:flex;align-items:center;gap:10px;font-size:20px;font-weight:500;color:var(--red)}
.social-box .head .mark{width:18px;height:18px;background:var(--red)}
.social-box .like{margin-left:auto;font-size:12px;color:var(--ink);border:1px solid var(--line);padding:4px 10px;border-radius:3px;font-weight:400}
.social-box .fans{margin-top:20px;width:300px;height:150px;background:linear-gradient(135deg,#d8c0ad,#9c8475 60%,#6e625e)}

/* newsletter band */
.newsband{position:absolute;top:1920px;left:0;width:1200px;height:84px;background:var(--red);display:flex;align-items:center;padding:0 60px;color:var(--white)}
.socials{display:flex;gap:12px}
.socials span{width:36px;height:36px;border-radius:50%;border:2px solid var(--white)}
.news-title{margin-left:150px;font-size:20px;font-weight:500}
.news-title small{display:block;font-size:11px;font-weight:300;opacity:.85;margin-top:2px}
.news-form{margin-left:24px;display:flex}
.news-form .field{width:300px;height:40px;background:var(--white);color:var(--muted);font-size:13px;display:flex;align-items:center;padding-left:16px}
.news-form .submit{width:130px;height:40px;background:var(--navy);font-size:13px;font-weight:500;letter-spacing:1px;display:flex;align-items:center;justify-content:center}

/* tagline */
.tagline{position:absolute;top:2004px;left:0;width:1200px;height:216px;background:var(--white)}
.tagline h2{position:absolute;left:60px;top:60px;width:720px;font-size:24px;font-weight:500;line-height:1.4}
.tagline p{position:absolute;left:60px;top:140px;font-size:12px;color:var(--muted)}
.tagline .cta{position:absolute;left:840px;top:84px;display:flex;gap:20px}
.tagline .cta .btn{width:140px;height:46px;font-size:15px}

/* footer */
.footer{position:absolute;top:2220px;left:0;width:1200px;height:250px;background:var(--navy);color:#d8d9e2}
.col{position:absolute;top:40px;font-size:13px}
.col h4{color:var(--red);font-size:15px;font-weight:700;letter-spacing:1px;margin-bottom:26px;height:18px}
.col li{margin-bottom:14px}
.c1{left:80px}
.c2{left:280px}
.c3{left:520px}
.c4{left:780px}
.c5{left:960px}
.bottombar{position:absolute;top:2470px;left:0;width:1200px;height:50px;background:var(--red);color:var(--white);font-size:12px;display:flex;align-items:center;justify-content:center}
.bottombar .up{position:absolute;right:30px;width:28px;height:28px;background:var(--red-dark);display:flex;align-items:center;justify-content:center}
</style>
</head>
<body>
<div class="page">

  <header class="topnav">
    <a class="how" href="#"><i></i>HOW IT WORKS?</a>
    <a class="btn btn-navy" href="#">BUY</a>
    <a class="btn btn-red" href="#">SELL</a>
    <a class="link register" href="#">REGISTER</a>
    <a class="link" href="#">LOGIN</a>
  </header>

  <section class="hero">
    <div class="hero-panel">
      <div class="hero-devices" role="img" aria-label="Line illustration of a monitor, laptop, tablet and phone"></div>
      <div class="brand"><span class="mark"></span>ourTradeLoop</div>
      <p class="hero-copy">It is a platform that enables users to sell their old electronics for cash, either for themselves or they can donate the cash to charity.</p>
      <div class="hero-actions">
        <a class="btn btn-navy" href="#">BUY</a>
        <span>or</span>
        <a class="btn btn-navy" href="#">SELL</a>
      </div>
    </div>
    <div class="hero-photo" role="img" aria-label="Photo of two smiling young people looking at their smartphones outdoors"></div>
  </section>

  <div class="tabs"><span class="tab-buy">BUY</span><span class="tab-sell">SELL</span></div>
  <div class="tab-rule"></div>

  <div class="product phone-a">
    <div class="shot" role="img" aria-label="Product photo of a smartphone"></div>
    OTHER PHONES
  </div>
  <div class="product phone-b">
    <div class="shot" role="img" aria-label="Product photo of a Q-Phone"></div>
    Q-PHONES
  </div>
  <div class="product pad">
    <div class="shot" role="img" aria-label="Product photo of a Q-Pad tablet"></div>
    Q-PADS
  </div>
  <div class="product book">
    <div class="shot" role="img" aria-label="Product photo of a Q-Book laptop"></div>
    Q-BOOKS
  </div>

  <section class="why">
    <h2>WHY CUSTOMERS CHOOSE US</h2>
    <div class="rule"></div>
    <div class="feature feature-delivery">
      <svg width="60" height="60" viewBox="0 0 60 60" aria-hidden="true"><path d="M4 28 56 6 40 54 28 36 52 12 22 32Z" fill="#ea2a33"/></svg>
      <h3>FAST &amp; FREE DELIVERY</h3>
      <p>Book a free courier or drop your parcel at a local shop. We cover the postage and get your item here fast.</p>
    </div>
    <div class="feature feature-payment">
      <svg width="60" height="60" viewBox="0 0 60 60" aria-hidden="true"><path d="M20 28V18a10 10 0 0 1 20 0" fill="none" stroke="#ea2a33" stroke-width="6"/><rect x="12" y="28" width="36" height="28" rx="3" fill="#ea2a33"/><rect x="28" y="36" width="4" height="10" fill="#fff"/></svg>
      <h3>SAFE &amp; SECURE PAYMENT</h3>
      <p>Every payment runs through a protected checkout, and your old data is wiped clean before any device is resold.</p>
    </div>
    <div class="feature feature-refund">
      <svg width="60" height="60" viewBox="0 0 60 60" aria-hidden="true"><rect x="2" y="14" width="56" height="32" rx="2" fill="#ea2a33"/><circle cx="30" cy="30" r="10" fill="#fff"/><rect x="28" y="24" width="4" height="12" fill="#ea2a33"/></svg>
      <h3>100% MONEY BACK GUARANTEED</h3>
      <p>If our quote changes once we check your device, you can ask for it back and pay nothing at all.</p>
    </div>
  </section>

  <section class="tweets">
    <h2>Latest Tweets</h2>
    <div class="arrows"><span>&#8249;</span><span>&#8250;</span></div>
    <div class="rule"></div>
    <article class="tweet tweet-first">
      <div class="who"><span class="avatar"></span><div><div class="name">ourTradeLoop</div><div class="handle">@ourtradeloop</div></div><span class="time">2h</span></div>
      <p>Just traded my old tablet for cash in under a week. Simple process, quick payment and friendly support team.</p>
    </article>
    <article class="tweet tweet-second">
      <div class="who"><span class="avatar"></span><div><div class="name">ourTradeLoop</div><div class="handle">@ourtradeloop</div></div><span class="time">5h</span></div>
      <p>Donated the cash from my old phone to a local charity today. Great to see gadgets put to good use.</p>
    </article>
  </section>

  <aside class="social-box">
    <div class="head"><span class="mark"></span>ourTradeLoop<span class="like">Like</span></div>
    <div class="fans" role="img" aria-label="Grid of follower profile photos"></div>
  </aside>

  <section class="newsband">
    <div class="socials"><span></span><span></span><span></span><span></span><span></span></div>
    <div class="news-title">Join Our Newsletter<small>Get latest news and updates</small></div>
    <div class="news-form"><span class="field">Enter Your Email Address</span><span class="submit">SUBSCRIBE</span></div>
  </section>

  <section class="tagline">
    <h2>It is a platform that enables users to sell their electronics for cash, either for themselves or they can donate the cash to charity.</h2>
    <p>Clear your drawers of old gadgets, get a fair price and choose where the money goes.</p>
    <div class="cta"><a class="btn btn-navy" href="#">BUY</a><a class="btn btn-red" href="#">SELL</a></div>
  </section>

  <footer class="footer">
    <div class="col c1"><h4>POPULAR SEARCHES</h4><ul><li>Sell My Cell Phone</li><li>Sell Your Q-Phone</li><li>Sell Nordvik Astra</li><li>Q-Book Trade In</li><li>Sell Corvel</li></ul></div>
    <div class="col c2"><h4></h4><ul><li>Sell My Cell Phone</li><li>Sell Your Q-Phone</li><li>Sell Nordvik Astra</li><li>Q-Book Trade In</li><li>Sell Corvel</li></ul></div>
    <div class="col c3"><h4></h4><ul><li>Sell My Cell Phone</li><li>Sell Your Q-Phone</li><li>Sell Nordvik Astra</li><li>Q-Book Trade In</li><li>Sell Corvel</li></ul></div>
    <div class="col c4"><h4>HELP</h4><ul><li>How It Works</li><li>Contact Us</li><li>Support &amp; FAQs</li><li>Find a Parcel Shop</li></ul></div>
    <div class="col c5"><h4>LEGAL</h4><ul><li>Privacy Policy</li><li>Terms and Conditions</li><li>Print Courier T&amp;Cs</li><li>Free Send Service T&amp;Cs</li><li>Smart Send Service T&amp;Cs</li></ul></div>
  </footer>
  <div class="bottombar">ourTradeLoop &copy; 2016 All Rights Reserved<span class="up">&#8963;</span></div>

</div>
</body>
</html>
```